Stationery Design Project for Nimbora, Chicago

Nimbora, a street parking application which helps car drivers find a street parking spot by offering an ideal path along which to look for parking. This path is calculated by our algorithm based on data (e.g. historical data, baseball games schedule, etc.). Along this path the driver will find a spot and will also save 70% of the search time. Customer we target is reg. between 21 and 45 yo.

We envision something young, fresh, bright and original. Slightly abstract maybe. It should represent the idea and elements of finding street parking in the city, e.g. car(s), parking spot, people, city, etc. (just ideas!).

Logo is attached.

Requirement:
- Business Cards (2 Sided Full Color CMYK)
- Letterhead (1 Sided Full Color CMYK)
- Envelope (1 Sided Full Color CMYK)
- Sticker (1 Sided Full Color CMYK), round with a 2inch diameter.

Reason: We're starting to get more and more designs and need more time to look into all of them. Very exciting!! Thanks to everybody!

Hi all, we're in the process of selecting our favs. Though choices!!! Really good submissions. Will keep you posted and sorry for the delay.

Target Market(s)

Car drivers and owners between 21 and 45

Industry/Entity Type

Parking

Requirements
Must have
• Sticker should be round and include company URL nimbora.com and the new logo which we will attach soon.
Should not have
• Should not be too serious or boring.

```html
<!DOCTYPE html>
<html lang="en">
<head>
<meta charset="utf-8">
<title>Nimbora Business Card</title>
<link href="https://fonts.googleapis.com/css2?family=Source+Sans+3:wght@400;600;700&display=swap" rel="stylesheet">
<style>
  :root {
    --backdrop: #ececec;
    --card-white: #ffffff;
    --blue-deep: #2a3f9c;
    --blue-mid: #2f63c0;
    --blue-light: #2f9be0;
    --ink-dark: #2b2b2b;
    --ink-grey: #555555;
    --name-blue: #2a3a8c;
    --photo-grey: #8d929a;
    --photo-light: #c9ccd2;
  }
  * { margin: 0; padding: 0; box-sizing: border-box; }
  html, body { width: 1200px; height: 758px; overflow: hidden; }
  body {
    background: var(--backdrop);
    font-family: "Source Sans 3", "Myriad Pro", sans-serif;
    position: relative;
  }
  .card {
    position: absolute;
    width: 540px;
    height: 310px;
    border-radius: 28px;
    overflow: hidden;
    box-shadow: 0 6px 18px rgba(0,0,0,0.18);
  }
  .card-front { left: 40px; top: 224px; background: var(--card-white); }
  .card-back {
    left: 620px; top: 224px;
    background: linear-gradient(180deg, var(--blue-deep) 0%, var(--blue-mid) 50%, var(--blue-light) 100%);
  }
  .front-waves { position: absolute; inset: 0; }
  .brand {
    position: absolute;
    display: flex;
    align-items: center;
    gap: 16px;
  }
  .brand-dot {
    border-radius: 50%;
    background: var(--blue-mid);
    flex: none;
  }
  .brand-name {
    font-weight: 600;
    color: var(--ink-dark);
    letter-spacing: 1px;
  }
  .card-front .brand { left: 42px; top: 34px; }
  .card-front .brand-dot { width: 80px; height: 80px; }
  .card-front .brand-name { font-size: 58px; }
  .address {
    position: absolute;
    left: 42px; top: 158px;
    font-size: 14px;
    color: var(--ink-grey);
  }
  .holder {
    position: absolute;
    left: 42px; top: 194px;
    font-size: 19px;
    font-weight: 700;
    color: var(--name-blue);
  }
  .holder .title { font-size: 14px; font-weight: 400; color: var(--ink-grey); }
  .contacts {
    position: absolute;
    right: 26px; top: 152px;
    list-style: none;
    text-align: right;
    color: var(--card-white);
    font-size: 14px;
    line-height: 19px;
  }
  .contacts li { display: flex; justify-content: flex-end; align-items: center; gap: 6px; }
  .contacts svg { width: 11px; height: 11px; fill: var(--card-white); }
  .card-back .brand { left: 44px; top: 112px; }
  .card-back .brand-dot { width: 70px; height: 70px; background: var(--card-white); }
  .card-back .brand-name { font-size: 40px; color: var(--card-white); }
  .street-photo {
    position: absolute;
    left: 292px; top: 62px;
    width: 228px; height: 196px;
    border-radius: 14px;
    background: radial-gradient(ellipse at 50% 50%, var(--photo-light) 0%, var(--photo-grey) 60%, rgba(141,146,154,0) 100%);
  }
</style>
</head>
<body>
  <section class="card card-front">
    <svg class="front-waves" viewBox="0 0 540 310" preserveAspectRatio="none" aria-hidden="true">
      <defs>
        <linearGradient id="waveBlue" x1="0" y1="0" x2="0" y2="1">
          <stop offset="0" stop-color="#2a3f9c"/>
          <stop offset="0.6" stop-color="#2f63c0"/>
          <stop offset="1" stop-color="#2f9be0"/>
        </linearGradient>
      </defs>
      <path d="M0,262 C170,300 300,200 540,62 L540,310 L0,310 Z" fill="url(#waveBlue)"/>
      <path d="M0,252 C170,290 290,192 430,116" fill="none" stroke="#1c1c1c" stroke-width="3"/>
      <path d="M0,285 C180,312 360,250 540,180 L540,310 L0,310 Z" fill="#3aa2e4" opacity="0.55"/>
    </svg>
    <div class="brand">
      <span class="brand-dot"></span>
      <span class="brand-name">nimbora</span>
    </div>
    <p class="address">Complex name, Street name, City, State, zip code</p>
    <p class="holder">Your Name, <span class="title">Title</span></p>
    <ul class="contacts">
      <li><svg viewBox="0 0 12 12"><path d="M3 1l2 2-1 1.5c.7 1.4 1.8 2.5 3.2 3.2L8.7 6.7l2 2-1.2 1.8C5.5 10.5 1.5 6.5 1.5 2.2z"/></svg>123-456-789</li>
      <li><svg viewBox="0 0 12 12"><rect x="3" y="0.5" width="6" height="11" rx="1.2"/></svg>123-456-789</li>
      <li><svg viewBox="0 0 12 12"><path d="M0.5 2.5h11v7h-11z M0.5 2.5l5.5 4 5.5-4" /></svg>info@nimbora.com</li>
      <li><svg viewBox="0 0 12 12"><circle cx="6" cy="6" r="5.5"/></svg>www.nimbora.com</li>
    </ul>
  </section>

  <section class="card card-back">
    <div class="brand">
      <span class="brand-dot"></span>
      <span class="brand-name">nimbora</span>
    </div>
    <div class="street-photo" role="img" aria-label="Photo of cars parked in marked street parking bays seen from above"></div>
  </section>
</body>
</html>
```